Accountability Project Graphics

I want to create 10 social media graphics (new Instagram size 4:5 (1080 x 1350 pixels) focusing on our Quilvo Accountability App, using any of the 3 pictures attached. Use the attached pics only, NO RANDOM STOCK PHOTOGRAPHY. For the color scheme, use the landing page colors/fonts (attached).
You can add any of the 3 photos attached but I mainly need BOLD text that includes these headlines and sub-headlines on them.
Please NOTE for all the headlines below, also add this sub-headline on each graphic:
Stay Consistent with RT in Your Pocket!
Here are the headlines:
• Stop Starting Over Every Monday
• You don't need more willpower. You need more support
• Built for women who are tired of doing this alone
• When Motivation Fades, RT Checks In
• The Support System You've Been Missing
• Support When Motivation Disappears
• What if RT Checked in Every Day?
• The Missing Piece Isn't Another Diet
• Eat the food you love. Stay accountable every day.
• One Bad Meal Doesn't Mean You Failed
women over 40 trying to lose weight

```html
<!DOCTYPE html>
<html lang="en">
<head>
<meta charset="utf-8">
<title>Accountability Project Graphics</title>
<link rel="stylesheet" href="https://fonts.googleapis.com/css2?family=DM+Serif+Display&family=Roboto+Condensed:wght@500;700;800&display=swap">
<style>
  :root{
    --stage:#3a3a3a;
    --plum:#2d1a3d;
    --pink:#d4467c;
    --blush-top:#fdf1f5;
    --blush-bottom:#f4c4d5;
    --white:#ffffff;
    --photo-warm:#c9a4b4;
    --photo-dark:#3b2b3d;
    --photo-store:#e7c6d6;
  }
  *{margin:0;padding:0;box-sizing:border-box}
  html,body{width:1200px;height:616px;overflow:hidden;background:var(--stage)}
  .board{position:relative;width:1200px;height:616px}
  .card{position:absolute;width:214px;height:267px;overflow:hidden;
    background:linear-gradient(180deg,var(--blush-top) 0%,var(--blush-bottom) 100%)}
  .r1{top:32px}.r2{top:314px}
  .c1{left:36px}.c2{left:266px}.c3{left:497px}.c4{left:723px}.c5{left:952px}
  .photo{position:absolute}
  .photo--portrait{background:linear-gradient(90deg,rgba(244,196,213,0) 0%,var(--photo-warm) 30%,var(--photo-dark) 70%)}
  .photo--hug{background:linear-gradient(180deg,var(--photo-store) 0%,var(--photo-warm) 55%,var(--photo-dark) 100%)}
  .photo--duo{background:linear-gradient(180deg,#e8d9cf 0%,#b79a92 40%,#3c3a55 100%)}
  .fade-bottom{-webkit-mask-image:linear-gradient(180deg,#000 65%,transparent 100%);mask-image:linear-gradient(180deg,#000 65%,transparent 100%)}
  .fade-top{-webkit-mask-image:linear-gradient(0deg,#000 70%,transparent 100%);mask-image:linear-gradient(0deg,#000 70%,transparent 100%)}
  .ln{position:absolute;left:0;right:0;text-align:center;white-space:nowrap;line-height:1}
  .serif{font-family:"DM Serif Display",Georgia,serif;letter-spacing:-0.02em}
  .sans{font-family:"Roboto Condensed","Arial Narrow",sans-serif;font-weight:800}
  .sans-md{font-family:"Roboto Condensed","Arial Narrow",sans-serif;font-weight:500}
  .pink{color:var(--pink)}.plum{color:var(--plum)}
  .rule{position:absolute;height:1px;background:var(--plum)}
  .dash::before,.dash::after{content:"";display:inline-block;width:14px;height:1.5px;background:currentColor;vertical-align:middle;margin:0 5px}
  .pill{position:absolute;left:50%;transform:translateX(-50%);height:18px;padding:0 8px;border-radius:99px;background:var(--white);
    font-family:"Roboto Condensed","Arial Narrow",sans-serif;font-weight:700;font-size:9px;line-height:18px;color:var(--plum);white-space:nowrap;
    box-shadow:0 1px 3px rgba(45,26,61,.12)}
  .pill span{color:var(--pink)}
  .tag{font-family:"Roboto Condensed","Arial Narrow",sans-serif;font-weight:700;color:var(--plum)}
  .tag span{color:var(--pink)}
  .left .ln{text-align:left;left:14px}
  .right .ln{text-align:center;left:96px;right:8px}
</style>
</head>
<body>
<main class="board">

  <!-- Stop Starting Over -->
  <section class="card r1 c1 left">
    <div class="photo photo--portrait" style="left:120px;top:0;width:94px;height:267px" role="img" aria-label="Smiling coach in black mesh top leaning on a counter"></div>
    <div class="ln serif pink" style="top:20px;font-size:42px">STOP</div>
    <div class="ln sans plum" style="top:62px;font-size:25px">STARTING</div>
    <div class="ln serif plum" style="top:86px;font-size:34px">OVER</div>
    <div class="ln serif pink" style="top:120px;font-size:31px">EVERY</div>
    <div class="ln serif pink" style="top:148px;font-size:32px">Monday</div>
    <div class="rule" style="left:15px;top:184px;width:37px"></div>
    <div class="ln tag" style="top:191px;font-size:10.5px;line-height:13px">Stay Consistent with<br><span>RT in Your Pocket!</span></div>
  </section>

  <!-- Willpower / Support -->
  <section class="card r1 c2">
    <div class="photo photo--hug" style="left:0;top:0;width:214px;height:130px" role="img" aria-label="Two women hugging and laughing in a store"></div>
    <div class="ln sans plum dash" style="top:144px;font-size:12px">YOU DON'T NEED MORE</div>
    <div class="ln serif pink" style="top:157px;font-size:25px">WILLPOWER</div>
    <div class="ln sans plum" style="top:182px;font-size:23px">YOU NEED MORE</div>
    <div class="ln serif pink" style="top:202px;font-size:35px">SUPPORT</div>
    <div class="pill" style="top:242px">Stay Consistent with <span>RT in Your Pocket!</span></div>
  </section>

  <!-- Built for Women -->
  <section class="card r1 c3">
    <div class="photo photo--duo" style="left:0;top:152px;width:214px;height:115px" role="img" aria-label="Two women smiling side by side in denim jackets"></div>
    <div class="ln serif plum" style="top:18px;font-size:29px">BUILT FOR</div>
    <div class="ln serif pink" style="top:44px;font-size:35px">WOMEN</div>
    <div class="rule" style="left:29px;top:78px;width:156px"></div>
    <div class="ln sans-md plum" style="top:81px;font-size:13.5px">Who are tired of doing this</div>
    <div class="rule" style="left:29px;top:96px;width:156px"></div>
    <div class="ln serif pink" style="top:96px;font-size:42px">ALONE</div>
    <div class="pill" style="top:141px">Stay Consistent with <span>RT in Your Pocket!</span></div>
  </section>

  <!-- When Motivation Fades -->
  <section class="card r1 c4">
    <div class="photo photo--portrait fade-bottom" style="left:55px;top:8px;width:104px;height:140px;background:linear-gradient(180deg,var(--photo-dark),var(--photo-warm))" role="img" aria-label="Smiling coach in black mesh top, hand on hip"></div>
    <div class="ln sans plum dash" style="top:133px;font-size:27px">WHEN</div>
    <div class="ln serif pink" style="top:160px;font-size:26px">MOTIVATION</div>
    <div class="ln sans plum" style="top:184px;font-size:27px">FADES</div>
    <div class="ln serif pink" style="top:209px;font-size:26px">RT CHECKS IN</div>
    <div class="pill" style="top:239px">Stay Consistent with <span>RT in Your Pocket!</span></div>
  </section>

  <!-- Support System -->
  <section class="card r1 c5">
    <div class="photo photo--hug fade-bottom" style="left:0;top:0;width:214px;height:160px" role="img" aria-label="Two women hugging and laughing in a store"></div>
    <div class="ln sans-md plum dash" style="top:151px;font-size:15px">The Support System</div>
    <div class="ln serif plum" style="top:171px;font-size:27px">YOU'VE BEEN</div>
    <div class="ln serif pink" style="top:196px;font-size:38px">MISSING</div>
    <div class="pill" style="top:239px">Stay Consistent with <span>RT in Your Pocket!</span></div>
  </section>

  <!-- Support When Motivation Disappears -->
  <section class="card r2 c1">
    <div class="photo photo--duo fade-bottom" style="left:0;top:0;width:214px;height:160px" role="img" aria-label="Two women smiling side by side in denim jackets"></div>
    <div class="ln sans plum" style="top:153px;font-size:23px">SUPPORT WHEN</div>
    <div class="rule" style="left:20px;top:178px;width:174px"></div>
    <div class="ln serif pink" style="top:181px;font-size:27px">MOTIVATION</div>
    <div class="ln serif plum" style="top:206px;font-size:27px">DISAPPEARS</div>
    <div class="pill" style="top:238px">Stay Consistent with <span>RT in Your Pocket!</span></div>
  </section>

  <!-- What if RT Checked In -->
  <section class="card r2 c2 left">
    <div class="photo photo--portrait" style="left:128px;top:132px;width:86px;height:135px;background:linear-gradient(180deg,var(--photo-warm),var(--photo-dark))" role="img" aria-label="Smiling coach in black mesh top"></div>
    <div class="ln serif plum" style="top:17px;font-size:37px;left:17px">What if <span class="pink">RT</span></div>
    <div class="ln serif pink" style="top:53px;font-size:48px;left:17px">Checked</div>
    <div class="ln serif plum" style="top:98px;font-size:37px;left:17px">IN EVERY</div>
    <div class="ln serif plum" style="top:133px;font-size:37px;left:17px">DAY?</div>
    <div style="position:absolute;left:14px;top:182px;width:122px;height:65px;background:var(--white);border-radius:33px 0 0 33px"></div>
    <div class="ln tag" style="top:191px;left:32px;font-size:12.5px;line-height:16px">Stay Consistent<br>with <span>RT in Your</span><br><span>Pocket!</span></div>
  </section>

  <!-- Missing Piece -->
  <section class="card r2 c3">
    <div class="photo photo--hug fade-top" style="left:0;top:128px;width:214px;height:139px" role="img" aria-label="Two women hugging and laughing in a store"></div>
    <div class="ln serif plum" style="top:18px;font-size:27px">THE MISSING</div>
    <div class="ln sans plum" style="top:45px;font-size:29px">PIECE ISN'T</div>
    <div class="ln serif pink" style="top:74px;font-size:30px">Another Diet</div>
    <div class="pill" style="top:109px">Stay Consistent with <span>RT in Your Pocket!</span></div>
  </section>

  <!-- Eat the Food -->
  <section class="card r2 c4">
    <div class="photo photo--duo fade-bottom" style="left:0;top:0;width:214px;height:150px" role="img" aria-label="Two women smiling side by side in denim jackets"></div>
    <div class="ln sans plum" style="top:139px;font-size:24px">EAT THE FOOD</div>
    <div class="ln serif pink dash" style="top:160px;font-size:24px">You Love.</div>
    <div class="ln serif pink" style="top:183px;font-size:22px">Stay Accountable</div>
    <div class="ln serif plum" style="top:204px;font-size:29px">EVERY DAY</div>
    <div class="pill" style="top:237px">Stay Consistent with <span>RT in Your Pocket!</span></div>
  </section>

  <!-- One Bad Meal -->
  <section class="card r2 c5 right">
    <div class="photo photo--portrait" style="left:0;top:0;width:100px;height:267px;background:linear-gradient(180deg,var(--photo-warm) 0%,var(--photo-dark) 45%)" role="img" aria-label="Smiling coach in black mesh top, hand on hip"></div>
    <div class="ln serif pink" style="top:20px;font-size:40px">ONE</div>
    <div class="ln serif pink" style="top:57px;font-size:42px">BAD</div>
    <div class="ln serif pink" style="top:96px;font-size:33px">MEAL</div>
    <div class="rule" style="left:98px;top:129px;width:100px;height:1.5px;background:var(--pink)"></div>
    <div class="ln sans plum" style="top:137px;font-size:26px">DOESN'T</div>
    <div class="ln sans plum" style="top:163px;font-size:37px">MEAN</div>
    <div class="ln sans plum" style="top:200px;font-size:22px">YOU FAILED</div>
    <div class="pill" style="top:237px">Stay Consistent with <span>RT in Your Pocket!</span></div>
  </section>

</main>
</body>
</html>
```